Website for Torvel Capital - investment banking firm

We have a corporate identity (thanks to Ravinka/31842) and want to extend that into a website design.  See the attached zipped files.
We have software folks in-house to do the coding.
See the attached Project Brief & Notes for more details.  Don't worry about the actual text - lorem ipsum will be fine.
The server will be Apache.
Thank you!
Desmond

Industry/Entity Type
Investment

```html
<!DOCTYPE html>
<html lang="en">
<head>
<meta charset="utf-8">
<title>Torvel Capital</title>
<link href="https://fonts.googleapis.com/css2?family=Source+Sans+3:ital,wght@0,400;0,600;0,700;1,400&family=Source+Serif+4:wght@400;600&display=swap" rel="stylesheet">
<style>
:root{
  --navy:#1d3d6e;
  --navy-dark:#16243a;
  --blue:#1f5ca8;
  --ink:#3b4654;
  --muted:#6d7580;
  --light:#f2f3f5;
  --line:#dfe2e6;
  --white:#ffffff;
  --gray-bar:#c9ccd1;
  --social:#8d939b;
}
*{margin:0;padding:0;box-sizing:border-box}
html,body{width:1200px;height:3514px;overflow:hidden}
body{font-family:"Source Sans 3",Arial,sans-serif;color:var(--ink);background:var(--white);position:relative}
section,header,footer{position:absolute;left:0;width:1200px}
.abs{position:absolute}
.center{text-align:center;left:0;width:1200px}
h2.section-title{font-size:32px;font-weight:400;letter-spacing:1px;color:var(--ink)}
.lede{font-size:15px;color:var(--muted);line-height:24px}

/* header */
.site-header{top:0;height:93px;background:var(--white);border-bottom:3px solid var(--navy)}
.brand{left:115px;top:22px;display:flex;align-items:center;gap:12px}
.brand-mark{width:38px;height:38px;background:var(--navy)}
.brand-name{font-size:30px;font-weight:600;color:var(--navy);letter-spacing:.5px}
.main-nav{right:170px;top:62px;display:flex;gap:26px;font-family:"Source Serif 4",Georgia,serif;font-size:15px;color:var(--navy-dark)}
.main-nav .active{color:var(--blue)}
.social-top{right:185px;top:12px;display:flex;gap:8px}
.social-top span{width:26px;height:26px;border-radius:50%;background:var(--blue);display:block}
.social-top span:nth-child(2){background:#6aa6d8}
.social-top span:nth-child(3){background:#e0672a}
.social-top span:nth-child(4){background:#55a149}

/* hero */
.hero{top:93px;height:480px;background:linear-gradient(120deg,#1a2a4a 0%,#3a4d74 40%,#5d5f86 60%,#2a2f4c 100%)}
.hero-photo{inset:0}
.hero-copy{left:205px;top:60px;color:var(--white)}
.hero-copy h1{font-size:42px;font-weight:400}
.hero-copy .tag{font-size:22px;font-weight:600;margin-top:2px}
.hero-copy p{font-size:16px;line-height:22px;margin-top:26px}
.btn{display:inline-block;background:var(--blue);color:var(--white);font-size:17px;text-transform:uppercase;padding:0 30px;line-height:48px}
.hero-copy .btn{margin-top:26px}

/* services */
.services{top:573px;height:527px;background:var(--light)}
.services .section-title{top:36px}
.services .lede{top:88px;left:200px;width:800px}
.service{top:240px;width:200px;text-align:center}
.service .icon{width:110px;height:110px;border-radius:50%;background:var(--white);margin:0 auto;display:flex;align-items:center;justify-content:center;box-shadow:0 1px 3px rgba(0,0,0,.08)}
.service h3{font-size:17px;font-weight:600;margin-top:28px}
.service p{font-size:13px;line-height:18px;color:var(--muted);margin-top:6px;padding:0 30px}
.pager{top:487px;left:555px;display:flex;gap:8px}
.pager span{width:38px;height:6px;background:var(--line);display:block}

/* pillars */
.pillars{top:1100px;height:440px;background:linear-gradient(110deg,#17284a 0%,#22406d 50%,#1d3358 100%)}
.pillar-images{left:185px;top:45px;width:310px;height:370px;background:linear-gradient(160deg,#d98b4a,#4f7fb8 50%,#59b5d8);clip-path:polygon(30% 0,100% 8%,100% 60%,60% 100%,10% 90%,0 30%)}
.pillars h2{left:545px;top:44px;font-size:26px;font-weight:600;color:#4e8ad6}
.pillars h2 em{font-style:normal;color:var(--white)}
.pillar-text{font-size:13px;line-height:18px;color:var(--white);width:350px}
.hexlabel{width:90px;height:80px;clip-path:polygon(25% 0,75% 0,100% 50%,75% 100%,25% 100%,0 50%);background:var(--white);color:var(--navy);font-size:26px;font-style:italic;display:flex;align-items:center;justify-content:center}

/* about */
.about{top:1540px;height:420px}
.about .section-title{top:55px}
.about .lede{top:110px}
.col-left{left:196px;top:170px;width:380px;font-size:13px;line-height:20px;color:var(--muted)}
.col-left p+p{margin-top:16px}
.col-head{font-size:14px;font-weight:700;color:var(--ink);margin-bottom:8px;text-transform:uppercase}
.col-right{left:612px;top:170px;width:398px}
.skill{height:19px;background:var(--gray-bar);margin-bottom:10px;position:relative}
.skill .fill{position:absolute;left:0;top:0;bottom:0;background:var(--navy)}
.skill .label{position:absolute;left:0;top:0;bottom:0;width:90px;background:var(--navy-dark);color:var(--white);font-size:11px;line-height:19px;padding-left:6px}
.divider{left:196px;top:385px;width:814px;height:1px;background:var(--line)}

/* team */
.team{top:1960px;height:440px}
.team .section-title{top:10px}
.member{top:75px;width:220px;text-align:center}
.member .portrait{width:150px;height:140px;margin:0 auto;clip-path:polygon(25% 0,75% 0,100% 50%,75% 100%,25% 100%,0 50%);background:linear-gradient(160deg,#c6ccd4,#6b7380)}
.member h3{font-size:17px;font-weight:600;margin-top:38px}
.member p{font-size:13px;line-height:18px;color:var(--muted);margin-top:6px;padding:0 20px}
.member .social{display:flex;gap:5px;justify-content:center;margin-top:14px}
.member .social span{width:24px;height:24px;border-radius:50%;background:var(--social);display:block}

/* testimonial */
.testimonial{top:2400px;height:435px;background:linear-gradient(180deg,#1c1b2c 0%,#3a2b3e 50%,#7a4a3a 100%)}
.testimonial h2{top:165px;font-size:23px;font-weight:600;color:var(--white);letter-spacing:.5px}
.testimonial .quote{top:208px;left:260px;width:680px;text-align:center;font-size:15px;font-style:italic;line-height:20px;color:var(--white)}
.qmark{top:190px;font-size:60px;color:var(--white);font-family:"Source Serif 4",Georgia,serif}
.testimonial .btn{top:265px;left:526px;background:var(--navy-dark);font-size:16px;text-transform:none;line-height:48px;padding:0 34px;position:absolute}

/* contact */
.contact{top:2835px;height:478px}
.map{inset:0;background:linear-gradient(135deg,#b7d3e6 0%,#cfe0c4 40%,#e3d8b4 60%,#a9cbe3 100%)}
.contact-panel{left:606px;top:45px;width:322px;height:365px;background:rgba(22,36,58,.94);padding:22px 18px;color:var(--white)}
.contact-panel .phone{font-size:20px}
.contact-panel .email{font-size:15px;margin-top:6px}
.contact-panel .social{display:flex;gap:6px;margin-top:14px}
.contact-panel .social span{width:24px;height:24px;border-radius:50%;background:#5a8fd0;display:block}
.field-row{display:flex;gap:8px;margin-top:26px}
.field{background:var(--white);color:var(--muted);font-size:11px;height:26px;line-height:26px;padding-left:6px;flex:1}
.field.message{height:90px;line-height:20px;margin-top:8px}
.send{display:inline-block;background:var(--blue);font-size:12px;padding:0 12px;line-height:24px;margin-top:18px}

/* footer */
.site-footer{top:3313px;height:201px;background:var(--white)}
.footer-name{top:70px;font-size:30px;color:var(--ink)}
.footer-line{top:130px;left:400px;width:400px;height:1px;background:var(--line)}
.copyright{top:162px;font-size:11px;color:var(--muted);letter-spacing:.5px}
</style>
</head>
<body>

<header class="site-header">
  <div class="brand abs"><span class="brand-mark"></span><span class="brand-name">Torvel Capital</span></div>
  <div class="social-top abs"><span></span><span></span><span></span><span></span></div>
  <nav class="main-nav abs">
    <span class="active">Home</span><span>About</span><span>Services</span><span>Current Engagements</span><span>Completed Transactions</span>
  </nav>
</header>

<section class="hero">
  <div class="hero-photo abs" role="img" aria-label="Night city skyline with a hand holding a smartphone"></div>
  <div class="hero-copy abs">
    <h1>Welcome</h1>
    <div class="tag">Lorem Ipsum is simply dummy text</div>
    <p>Lorem Ipsum is simply dummy text of the printing and typesetting<br>Lorem Ipsum is simply dummy text of the printing</p>
    <span class="btn">Get it now</span>
  </div>
</section>

<section class="services">
  <h2 class="section-title abs center">OUR SERVICES</h2>
  <p class="lede abs" style="text-align:center">Lorem Ipsum is simply dummy text of the printing and typesetting industry. Lorem Ipsum has been the industry's standard dummy text ever since the 1500s</p>

  <div class="service abs" style="left:200px">
    <div class="icon"><svg width="40" height="48" viewBox="0 0 40 48"><rect x="4" y="2" width="32" height="44" rx="5" fill="var(--navy)"/><rect x="8" y="7" width="24" height="32" fill="var(--white)"/><circle cx="20" cy="42" r="2" fill="var(--white)"/></svg></div>
    <h3>LOREM IPSUM</h3><p>Lorem Ipsum is simply dummy text of the printing and typesetting</p>
  </div>
  <div class="service abs" style="left:393px">
    <div class="icon"><svg width="54" height="48" viewBox="0 0 54 48"><rect x="2" y="4" width="50" height="32" rx="3" fill="var(--navy)"/><rect x="6" y="8" width="42" height="24" fill="var(--white)"/><rect x="22" y="36" width="10" height="6" fill="var(--navy)"/><rect x="14" y="42" width="26" height="4" fill="var(--navy)"/></svg></div>
    <h3>LOREM IPSUM</h3><p>Lorem Ipsum is simply dummy text of the printing and typesetting</p>
  </div>
  <div class="service abs" style="left:598px">
    <div class="icon"><svg width="48" height="48" viewBox="0 0 48 48"><circle cx="24" cy="24" r="21" fill="var(--navy)"/><path d="M12 14c6 2 8 8 4 12s2 8 0 12M30 8c-2 6 4 8 8 10s2 10-4 12-2 8 0 10" stroke="var(--white)" stroke-width="3" fill="none"/></svg></div>
    <h3>LOREM IPSUM</h3><p>Lorem Ipsum is simply dummy text of the printing and typesetting</p>
  </div>
  <div class="service abs" style="left:797px">
    <div class="icon"><svg width="50" height="44" viewBox="0 0 50 44"><g fill="var(--navy)"><rect x="2" y="2" width="10" height="10"/><rect x="16" y="2" width="32" height="10"/><rect x="2" y="17" width="10" height="10"/><rect x="16" y="17" width="32" height="10"/><rect x="2" y="32" width="10" height="10"/><rect x="16" y="32" width="32" height="10"/></g></svg></div>
    <h3>LOREM IPSUM</h3><p>Lorem Ipsum is simply dummy text of the printing and typesetting</p>
  </div>
  <div class="pager abs"><span></span><span></span></div>
</section>

<section class="pillars">
  <div class="pillar-images abs" role="img" aria-label="Cluster of hexagonal photos showing the firm's work"></div>
  <h2 class="abs">Our <em>three</em> pillars</h2>

  <p class="pillar-text abs" style="left:545px;top:112px">Lorem Ipsum is simply dummy text of the printing and typesetting industry. Lorem Ipsum has been the industry's standard dummy text ever since the 1500s.</p>
  <div class="hexlabel abs" style="left:920px;top:110px">one</div>

  <div class="hexlabel abs" style="left:545px;top:212px">two</div>
  <p class="pillar-text abs" style="left:660px;top:222px">Lorem Ipsum is simply dummy text of the printing and typesetting industry. Lorem Ipsum has been the industry's standard dummy text ever since the 1500s.</p>

  <p class="pillar-text abs" style="left:545px;top:330px">Lorem Ipsum is simply dummy text of the printing and typesetting industry. Lorem Ipsum has been the industry's standard dummy text ever since the 1500s.</p>
  <div class="hexlabel abs" style="left:920px;top:328px">three</div>
</section>

<section class="about">
  <h2 class="section-title abs center">ABOUT TORVEL CAPITAL</h2>
  <p class="lede abs center">Lorem Ipsum is simply dummy text of the printing and typesetting industry. Lorem Ipsum has been the industry'</p>
  <div class="col-left abs">
    <div class="col-head">Years of experience</div>
    <p>Lorem Ipsum is simply dummy text of the printing and typesetting industry. Lorem Ipsum has been the industry's standard dummy text ever since the 1500s, when an unknown printer took a galley of type and scrambled it to make.</p>
    <p>It was popularised in the 1960s with the release of Letraset sheets containing Lorem Ipsum passages, and more recently</p>
  </div>
  <div class="col-right abs">
    <div class="col-head">Skills</div>
    <div class="skill"><span class="fill" style="width:90%"></span><span class="label">Lorem Ipsum</span></div>
    <div class="skill"><span class="fill" style="width:80%"></span><span class="label">Lorem Ipsum</span></div>
    <div class="skill"><span class="fill" style="width:72%"></span><span class="label">Lorem Ipsum</span></div>
    <div class="skill"><span class="fill" style="width:80%"></span><span class="label">Lorem Ipsum</span></div>
    <div class="skill"><span class="fill" style="width:90%"></span><span class="label">Lorem Ipsum</span></div>
  </div>
  <div class="divider abs"></div>
</section>

<section class="team">
  <h2 class="section-title abs center">MEET THE TEAM</h2>
  <div class="member abs" style="left:190px">
    <div class="portrait" role="img" aria-label="Team member portrait"></div>
    <h3>LOREM IPSUM</h3><p>Lorem Ipsum is simply dummy text of the printing and typesetting industry.</p>
    <div class="social"><span></span><span></span><span></span><span></span></div>
  </div>
  <div class="member abs" style="left:390px">
    <div class="portrait" role="img" aria-label="Team member portrait"></div>
    <h3>LOREM IPSUM</h3><p>Lorem Ipsum is simply dummy text of the printing and typesetting industry.</p>
    <div class="social"><span></span><span></span><span></span><span></span></div>
  </div>
  <div class="member abs" style="left:595px">
    <div class="portrait" role="img" aria-label="Team member portrait"></div>
    <h3>LOREM IPSUM</h3><p>Lorem Ipsum is simply dummy text of the printing and typesetting industry.</p>
    <div class="social"><span></span><span></span><span></span><span></span></div>
  </div>
  <div class="member abs" style="left:802px">
    <div class="portrait" role="img" aria-label="Team member portrait"></div>
    <h3>LOREM IPSUM</h3><p>Lorem Ipsum is simply dummy text of the printing and typesetting industry.</p>
    <div class="social"><span></span><span></span><span></span><span></span></div>
  </div>
</section>

<section class="testimonial" role="img" aria-label="Starry night sky fading to a warm horizon">
  <h2 class="abs center">KNOW WHAT? OUR CLIENT ARE SAYING THAT ...</h2>
  <span class="qmark abs" style="left:200px">&ldquo;</span>
  <p class="quote abs">Lorem Ipsum is simply dummy text of the printing and typesetting industry. Lorem Ipsum has been the industry's standard dummy text ever since the</p>
  <span class="qmark abs" style="left:970px">&rdquo;</span>
  <span class="btn">Lorem Ipsum</span>
</section>

<section class="contact">
  <div class="map abs" role="img" aria-label="World map showing office location"></div>
  <div class="contact-panel abs">
    <div class="phone">555.014.2290</div>
    <div class="email">contact@torvelcapital.com</div>
    <div class="social"><span></span><span></span><span></span><span></span></div>
    <div class="field-row"><div class="field">FULL NAME</div><div class="field">EMAIL</div></div>
    <div class="field message">MESSAGE</div>
    <span class="send">SEND</span>
  </div>
</section>

<footer class="site-footer">
  <div class="footer-name abs center">Torvel Capital</div>
  <div class="footer-line abs"></div>
  <div class="copyright abs center">COPYRIGHT&copy;2016, ALL RIGHTS RESERVED</div>
</footer>

</body>
</html>
```